Business Card Design

I need a logo and a business card design that can be used for my business stationary, Facebook page and in the future a website. I don't know if I need a large design for brochures and stationery and a small portion of that as the logo or business card design. I probably need some advice about that. My new company is called Willowbank Family Circle. I don't have all of my business contact details available yet, but I want to get the design ready, so that when all this information is available I can get the printing done quickly.I'm a social worker and my business will be providing parenting groups and counselling sessions for parents.I would like the logo and business card to be very feminine and pretty. I want a silhouette image of a Mother and Baby and decorative swirls of flowers/vines/leaves and butterflies.I have found some designs elsewhere that are along the lines of what I am looking for. These images are attached below, but the quality of these attachments is very poor as I photographed them with my phone.My preferred colours would be to use black and white, purple and/or pink, aqua and or blue/green.There are four logo/business card options attached. Logo option 1 - I really like the flower and vine design. Logo option 2 - again I like the flowers and leaf design and the use of colour and the silhouette image of the Mum and Baby; Logo option 3 - I like the butterflies and decorative swirls in this option and Logo option 4 - I think this design is the best for a logo. I love the mother and baby image. I don't like the tree branch and the birds but I like the way the hair has been incorporated into the branch. I prefer the design of the flowers/vine/leaves in the other options.

Industry/Entity Type

Business

Contact Information for Business Card

Company Name:Embrace Attachment ParentingMobile:0417 751 394Email:Currently sourcing - TBAContact Name:Janelle ApplegarthQualifications:Currently sourcing details - TBA

Font styles to use
Script

Colors
33a6d7
85cae6
886aae
6c459b
e667a6
eea4c8

Requirements
Must have
• My project must have an image of a mother and child, slightly encircled by the mother's hair perhaps in a heart shape, and the mother's hair becoming a beautiful filigree design of vine/leaves/flowers and with some butterfly somewhere.
• Can all of the Words be in the same font Attachment Parenting can be slightly smaller.
Nice to have
• I would like to also have a similar vine/leaves/flowers and maybe a butterfly on the opposite side of the card. Maybe the Mother/child image on the top left of the card and the other pattern on the bottom right.
• If possible the use of aqua, purple and pink.

```html
<!DOCTYPE html>
<html lang="en">
<head>
<meta charset="utf-8">
<title>Willowbank Family Circle – Business Card</title>
<link rel="stylesheet" href="https://fonts.googleapis.com/css2?family=Cinzel:wght@500&family=Source+Sans+3:wght@400&display=swap">
<style>
  :root {
    --teal-deep: #0f7482;
    --teal-bright: #14a0a6;
    --teal-mist: #e4eff1;
    --violet: #a347f5;
    --ink: #222326;
    --paper: #ffffff;
  }
  * { margin: 0; padding: 0; box-sizing: border-box; }
  html, body { width: 1200px; height: 686px; overflow: hidden; background: var(--paper); }
  .card {
    position: relative;
    width: 1200px;
    height: 686px;
    background: var(--paper);
    border: 1px solid var(--teal-bright);
    overflow: hidden;
    font-family: "Source Sans 3", "Myriad Pro", Arial, sans-serif;
  }
  .backdrop-mark {
    position: absolute;
    left: 640px;
    top: 130px;
    width: 540px;
    height: 540px;
    border-radius: 50%;
    background: var(--teal-mist);
  }
  .brand-dot {
    position: absolute;
    left: 268px;
    top: 50px;
    width: 160px;
    height: 160px;
    border-radius: 50%;
    background: var(--teal-deep);
  }
  .brand-name {
    position: absolute;
    left: 0;
    top: 296px;
    width: 680px;
    text-align: center;
    font-family: "Cinzel", "Trajan Pro", Georgia, serif;
    font-weight: 500;
    color: var(--teal-deep);
    line-height: 1;
  }
  .brand-name .line-one { display: block; font-size: 50px; letter-spacing: 1px; }
  .brand-name .line-two { display: block; font-size: 54px; letter-spacing: 1px; margin-top: 2px; }
  .brand-rule {
    position: absolute;
    left: 0;
    top: 417px;
    width: 636px;
    height: 10px;
    background: var(--teal-bright);
  }
  .contact {
    position: absolute;
    left: 34px;
    display: flex;
    align-items: center;
    font-size: 30px;
    color: var(--ink);
  }
  .contact svg { width: 50px; height: 42px; margin-right: 51px; flex: none; }
  .contact-email { top: 463px; }
  .contact-phone { top: 551px; }
  .person {
    position: absolute;
    left: 700px;
    top: 346px;
    width: 486px;
    text-align: center;
    color: var(--ink);
  }
  .person-name { font-size: 50px; line-height: 1; letter-spacing: 0.3px; }
  .person-title { font-size: 23px; color: var(--teal-bright); margin-top: 10px; letter-spacing: 0.5px; }
  .footer-band { position: absolute; left: 0; bottom: 0; width: 1200px; height: 47px; }
</style>
</head>
<body>
  <main class="card">
    <div class="backdrop-mark" aria-hidden="true"></div>

    <div class="brand-dot" aria-hidden="true"></div>
    <h1 class="brand-name">
      <span class="line-one">Willowbank</span>
      <span class="line-two">Family Circle</span>
    </h1>
    <div class="brand-rule" aria-hidden="true"></div>

    <p class="contact contact-email">
      <svg viewBox="0 0 50 36" aria-hidden="true">
        <rect x="1" y="1" width="48" height="34" fill="var(--teal-bright)"/>
        <path d="M1 1 L25 21 L49 1" fill="none" stroke="var(--paper)" stroke-width="2.5"/>
        <path d="M1 35 L19 16 M49 35 L31 16" fill="none" stroke="var(--paper)" stroke-width="2"/>
      </svg>
      <span>Currently Sourcing</span>
    </p>

    <p class="contact contact-phone">
      <svg viewBox="0 0 50 46" aria-hidden="true">
        <path d="M9 3 L17 1 L23 13 L17 18 C20 25 25 31 32 35 L37 29 L48 35 L46 43 C44 45 40 46 36 45 C22 40 10 29 4 14 C3 9 5 5 9 3 Z" fill="var(--teal-bright)"/>
      </svg>
      <span>0438 260 517</span>
    </p>

    <section class="person">
      <p class="person-name">Rosalind Thackeray</p>
      <p class="person-title">(DIRECTOR)</p>
    </section>

    <svg class="footer-band" viewBox="0 0 1200 47" preserveAspectRatio="none" aria-hidden="true">
      <polygon points="0,0 893,0 870,47 0,47" fill="var(--teal-deep)"/>
      <polygon points="912,0 1200,0 1200,47 887,47" fill="var(--violet)"/>
    </svg>
  </main>
</body>
</html>
```